Explosive, chemical reaction of creativity!

Web design for a digital marketing company. The unconventional is encouraged!
This is for a cool, young, geographically diverse company (sketchhive... you are all part of our team!!!)... we build websites but our real specialty is "search experience optimization".... creating conversion focused content, SEO (including content), and social media.

Target Market(s)

small to medium size businesses, law firms, medical practices, municipalities

Industry/Entity Type

Marketing

Number of Pages Required

2 page

Requirements
Must have
• WOW
• something different and special... we've been playing with a science theme (www.fernquillmedia.marketing) but we are open to different looks, layouts, etc.
• we nee a homepage design and an interior page design
• content needs to include: Marketing Catalysts (about us), Our Formula (services), Chemical Reactions(Results/Our Clients),
• FREE Online Prism Check
• Let us put together an objective snapshot of your digital presence for you.
Nice to have
• we are open to the use of background video (chemical reaction???)
• we are open to cool and different imagery
Should not have
• template look like most other websites

```html
<!DOCTYPE html>
<html lang="en">
<head>
<meta charset="utf-8">
<title>Fernquill Media Marketing</title>
<link rel="stylesheet" href="https://fonts.googleapis.com/css2?family=Source+Sans+3:wght@300;400;600;700&display=swap">
<style>
:root{
  --brand:#0d4f9c;
  --brand-dark:#083a75;
  --brand-bar:#1c63ad;
  --navy:#04101f;
  --ink:#333a44;
  --muted:#6b717a;
  --light:#f1f2f4;
  --white:#ffffff;
  --black:#0b0b0c;
}
*{box-sizing:border-box;margin:0;padding:0}
html,body{width:1200px;height:2419px;overflow:hidden}
body{position:relative;font-family:"Source Sans 3",Arial,sans-serif;color:var(--ink);background:var(--white)}
.abs{position:absolute}

/* header */
.site-header{left:0;top:0;width:1200px;height:94px;background:var(--white)}
.brand{left:170px;top:30px;display:flex;align-items:center;gap:12px}
.brand-mark{width:30px;height:30px;background:var(--brand-dark)}
.brand-name{font-size:25px;font-weight:700;letter-spacing:2px;color:var(--brand-dark);text-transform:uppercase}

.main-nav{left:0;top:94px;width:1200px;height:43px;background:linear-gradient(#2a6fb6,#0f4d92)}
.main-nav a,.footer-nav a{position:absolute;color:var(--white);text-decoration:none;font-size:13px}
.main-nav a{top:13px}

/* hero */
.hero{left:0;top:137px;width:1200px;height:465px;background:radial-gradient(ellipse at 72% 45%,#3f7fc2 0%,#163e72 28%,#07172d 60%,var(--navy) 100%)}
.hero-title{left:227px;top:252px;font-size:37px;font-weight:300;line-height:44px;color:var(--white)}
.hero-lead{left:227px;top:348px;width:420px;font-size:12.5px;line-height:16px;color:var(--white)}
.hero-features{left:227px;top:422px;font-size:17px;color:#3d86d4}
.hero-list{left:227px;top:452px;list-style:none;font-size:11.5px;color:var(--white)}
.hero-list li{height:22px;display:flex;align-items:center;gap:10px}
.slider-dots{left:206px;top:554px;display:flex;gap:16px}
.slider-dots span{width:32px;height:2px;background:#31557f}
.slider-dots span.active{background:#c9d4e2}

/* intro */
.intro-title{left:195px;top:628px;font-size:38px;font-weight:300;color:var(--brand-dark)}
.intro-highlight{left:198px;top:684px}
.intro-highlight span{display:block;width:max-content;margin-bottom:1px;padding:1px 8px;background:var(--brand);color:var(--white);font-size:19px;line-height:26.5px}
.intro-copy{left:200px;top:822px;width:385px;font-size:11.5px;line-height:19px;color:var(--ink)}
.intro-copy p+p{margin-top:19px}
.btn{display:inline-flex;align-items:center;justify-content:center;background:var(--brand-dark);color:var(--white);font-size:11px;border:0}
.intro-btn{left:200px;top:979px;width:100px;height:36px;box-shadow:0 2px 3px rgba(0,0,0,.3)}
.intro-visual{left:636px;top:666px;width:387px;height:318px;border-radius:8px;background:linear-gradient(#1f2328 0 6%,#3a6fa8 6% 77%,#c9c9cb 77% 84%,#e2e2e4 84%)}

/* features */
.features{left:0;top:1037px;width:1200px;height:361px;background:linear-gradient(100deg,#aec4dc 0%,#6f94bf 35%,#2f5f97 70%,#1c4a85 100%)}
.features-title{left:603px;top:1082px;font-size:36px;font-weight:300;color:var(--white)}
.accordion{left:602px;width:419px;background:var(--white)}
.accordion-head{height:45px;display:flex;align-items:center;justify-content:space-between;padding:0 18px;font-size:18px;color:var(--brand-dark)}
.accordion-body{background:#dfe4ea;padding:10px 18px;font-size:10.5px;line-height:19px;color:var(--muted);height:81px}
.accordion.open{top:1134px}
.accordion.closed{top:1269px}
.accordion.closed .accordion-head{height:68px;line-height:22px}

/* facts */
.facts-title{left:0;top:1426px;width:1200px;text-align:center;font-size:38px;font-weight:300;color:var(--brand-dark)}
.facts-sub{left:0;top:1475px;width:1200px;text-align:center;font-size:20px;color:var(--muted)}
.stat{top:1548px;display:flex;gap:10px}
.stat-icon{width:60px;height:60px;border-radius:50%;background:var(--brand-dark);display:flex;align-items:center;justify-content:center}
.stat-num{font-size:37px;font-weight:600;line-height:40px;color:var(--brand-dark)}
.stat-label{font-size:12px;line-height:14px;color:var(--muted)}

/* blog */
.blog{left:0;top:1689px;width:1200px;height:319px;background:var(--light);border-top:1px solid #e2e3e6}
.blog-title{left:0;top:1703px;width:1200px;text-align:center;font-size:36px;font-weight:300;color:var(--brand-dark)}
.post{top:1762px;width:270px}
.post-date{display:inline-block;background:var(--brand-dark);color:var(--white);font-size:10.5px;padding:2px 8px}
.post-title{margin-top:8px;font-size:19px;font-weight:400;line-height:23px;color:var(--brand-dark)}
.post-text{margin-top:8px;font-size:10px;line-height:13px;color:var(--ink)}
.post .btn{margin-top:10px;width:80px;height:26px;font-size:10px}

/* contact */
.contact{left:0;top:2008px;width:1200px;height:363px;background:linear-gradient(#1b66b2,#0c3f7c)}
.contact-title{left:202px;top:2040px;font-size:36px;font-weight:300;color:var(--white)}
.contact-sub{left:205px;top:2088px;font-size:19px;color:var(--white)}
.field{left:210px;width:306px;background:var(--white);font-size:12px;color:var(--ink);padding:8px 16px;text-transform:uppercase}
.field.name{top:2137px;height:33px}
.field.email{top:2174px;height:33px}
.field.message{top:2213px;height:84px}
.submit{left:210px;top:2311px;width:80px;height:28px;background:var(--black);font-size:10px}
.info{left:565px;color:var(--white)}
.info-head{display:flex;align-items:center;gap:12px;font-size:13px;text-transform:uppercase}
.info-text{margin:12px 0 0 23px;font-size:10px;line-height:17px;text-transform:uppercase}
.address{top:2095px}
.phones{top:2200px}
.online{top:2261px}
.socials{left:565px;top:2292px;display:flex;gap:6px}
.socials span{width:33px;height:33px;border-radius:50%;background:var(--white)}
.map{left:703px;top:2090px;width:321px;height:246px;border:3px solid var(--white);background:linear-gradient(135deg,#e4e8dc,#d6dccb 50%,#e8e6d6)}

/* footer */
.site-footer{left:0;top:2371px;width:1200px;height:48px;background:var(--black)}
.footer-nav a{top:17px;font-size:11px}
.copyright{left:769px;top:18px;font-size:10px;color:#7c7f85}
.page-mark{left:1057px;top:18px;font-size:11px;color:var(--white)}
</style>
</head>
<body>

<header class="site-header abs">
  <div class="brand abs"><span class="brand-mark"></span><span class="brand-name">Fernquill Media Marketing</span></div>
</header>

<nav class="main-nav abs">
  <a style="left:206px">Home</a>
  <a style="left:290px">Marketing Catalysts</a>
  <a style="left:445px">Our Formula</a>
  <a style="left:563px">Chemical Reactions</a>
  <a style="left:718px">Contact us</a>
</nav>

<section class="hero abs" role="img" aria-label="Glowing blue digital interface with a person reaching out amid holographic rings"></section>
<h1 class="hero-title abs">It's not rocket science,<br>it's Fernquill Media science!</h1>
<p class="hero-lead abs">Sales is the chemical reaction that results from "our formula" which is the right combination of our digital marketing services.</p>
<h2 class="hero-features abs" style="font-weight:400">Features</h2>
<ul class="hero-list abs">
  <li><svg width="12" height="8" viewBox="0 0 12 8"><path d="M0 4h10M7 1l3 3-3 3" stroke="#fff" stroke-width="1.5" fill="none"/></svg>FREE Online Prism Check</li>
  <li><svg width="12" height="8" viewBox="0 0 12 8"><path d="M0 4h10M7 1l3 3-3 3" stroke="#fff" stroke-width="1.5" fill="none"/></svg>Let us put together an objective snapshot of your digital presence for you.</li>
</ul>
<div class="slider-dots abs"><span></span><span class="active"></span><span></span></div>

<section class="intro">
  <h2 class="intro-title abs">Using data for success</h2>
  <div class="intro-highlight abs">
    <span>Search Engine Optimization</span>
    <span>has been replaced with</span>
    <span>Search Experience</span>
    <span>Optimization.</span>
  </div>
  <div class="intro-copy abs">
    <p>SALES is the end result of everything we do. It is why companies exists. It's why we market. It's why your business is online. Our job is to help you maximize your opportunity online to build your brand, get found by new customers and, ultimately, generate SALES!</p>
    <p>There's been a lot of talk the last few years about SEO, Search Engine Optimization. We believe that Search Engine Optimization has now been replaced with Search Experience Optimization.</p>
  </div>
  <span class="btn intro-btn abs">Read more</span>
  <div class="intro-visual abs" role="img" aria-label="Desktop monitor showing a person working with a futuristic data interface"></div>
</section>

<section class="features abs" role="img" aria-label="Hand holding a smartphone against a soft blurred blue backdrop"></section>
<h2 class="features-title abs" style="font-weight:300">Features</h2>
<div class="accordion open abs">
  <div class="accordion-head">FREE Online Prism Check
    <svg width="12" height="8" viewBox="0 0 12 8"><path d="M1 1l5 5 5-5" stroke="#083a75" stroke-width="2" fill="none"/></svg></div>
  <div class="accordion-body">Condimentum commodo ullamcorper lectus mauris elementum suspendisse elit adipiscing turpis tempus imperdiet dui ipsum nulla suspendisse facilisi eu sociis a malesuada eros justo at fusce sed hac.</div>
</div>
<div class="accordion closed abs">
  <div class="accordion-head"><span>Let us put together an objective snapshot<br>of your digital presence for you.</span>
    <svg width="8" height="12" viewBox="0 0 8 12"><path d="M1 1l5 5-5 5" stroke="#083a75" stroke-width="2" fill="none"/></svg></div>
</div>

<section class="facts">
  <h2 class="facts-title abs">Some Facts About Our Catalysts</h2>
  <p class="facts-sub abs">Working together to create change.</p>
  <div class="stat abs" style="left:178px">
    <span class="stat-icon"><svg width="30" height="26" viewBox="0 0 30 26"><rect x="1" y="6" width="28" height="19" rx="2" fill="#fff"/><path d="M10 6V2h10v4" stroke="#fff" stroke-width="2.5" fill="none"/><rect x="1" y="13" width="28" height="2" fill="#083a75"/></svg></span>
    <div><div class="stat-num">35</div><div class="stat-label">Years Combined<br>Marketing Experience</div></div>
  </div>
  <div class="stat abs" style="left:373px">
    <span class="stat-icon"><svg width="28" height="28" viewBox="0 0 28 28"><circle cx="11" cy="11" r="8" stroke="#fff" stroke-width="4" fill="none"/><path d="M17 17l8 8" stroke="#fff" stroke-width="5"/></svg></span>
    <div><div class="stat-num">10</div><div class="stat-label">Years Search Engine<br>Optimization Experience</div></div>
  </div>
  <div class="stat abs" style="left:597px">
    <span class="stat-icon"><svg width="30" height="26" viewBox="0 0 30 26"><rect x="2" y="2" width="26" height="17" stroke="#fff" stroke-width="2.5" fill="none"/><path d="M10 24h10M15 19v5" stroke="#fff" stroke-width="2.5"/></svg></span>
    <div><div class="stat-num">234</div><div class="stat-label">Websites created</div></div>
  </div>
  <div class="stat abs" style="left:820px">
    <span class="stat-icon"><svg width="32" height="26" viewBox="0 0 32 26"><circle cx="16" cy="7" r="5" fill="#fff"/><circle cx="6" cy="10" r="4" fill="#fff"/><circle cx="26" cy="10" r="4" fill="#fff"/><path d="M8 25a8 8 0 0116 0zM0 24a6 6 0 0110-4v4zM32 24a6 6 0 00-10-4v4z" fill="#fff"/></svg></span>
    <div><div class="stat-num">679</div><div class="stat-label">Amazing team</div></div>
  </div>
</section>

<section class="blog abs"></section>
<h2 class="blog-title abs">Blog</h2>
<article class="post abs" style="left:171px">
  <span class="post-date">May 14, 2016 &nbsp;| at 12:41</span>
  <h3 class="post-title">A Little Bird Told Me – 5 Reasons for Tweeting</h3>
  <p class="post-text">There's a thin red line between social media use and networking. Sometimes the two merge into a perfect harmony of conversation and resolution. Other times (perhaps too often), it's just cat pictures and quirky quotes.</p>
  <span class="btn">Read more</span>
</article>
<article class="post abs" style="left:463px">
  <span class="post-date">May 14, 2016 &nbsp;| at 12:41</span>
  <h3 class="post-title">The Revolution Will Now Be Optimized</h3>
  <p class="post-text">There's a thin red line between social media use and networking. Sometimes the two merge into a perfect harmony of conversation and resolution. Other times (perhaps too often), it's just cat pictures and quirky quotes.</p>
  <span class="btn">Read more</span>
</article>
<article class="post abs" style="left:758px">
  <span class="post-date">May 14, 2016 &nbsp;| at 12:41</span>
  <h3 class="post-title">Fast-Loading Tech Encourages New Standard ....</h3>
  <p class="post-text">There's a thin red line between social media use and networking. Sometimes the two merge into a perfect harmony of conversation and resolution. Other times (perhaps too often), it's just cat pictures and quirky quotes.</p>
  <span class="btn">Read more</span>
</article>

<section class="contact abs"></section>
<h2 class="contact-title abs">Contact Us</h2>
<p class="contact-sub abs">We can't wait to hear from you!</p>
<div class="field name abs">Name</div>
<div class="field email abs">Email</div>
<div class="field message abs">Message</div>
<span class="btn submit abs">SUBMIT</span>

<div class="info address abs">
  <div class="info-head"><svg width="10" height="14" viewBox="0 0 10 14"><path d="M5 0a5 5 0 00-5 5c0 4 5 9 5 9s5-5 5-9a5 5 0 00-5-5z" fill="#fff"/><circle cx="5" cy="5" r="2" fill="#1b66b2"/></svg>Address</div>
  <p class="info-text">2870 W. Alder Avenue<br>Suite 212<br>Brookfield, OR 97455</p>
</div>
<div class="info phones abs">
  <div class="info-head"><svg width="12" height="12" viewBox="0 0 12 12"><path d="M2 0l3 3-1.5 1.5a7 7 0 004 4L9 7l3 3-2 2C5 12 0 7 0 2z" fill="#fff"/></svg>Phones</div>
  <p class="info-text">855-310-4482</p>
</div>
<div class="info online abs">
  <div class="info-head"><svg width="12" height="12" viewBox="0 0 12 12"><circle cx="10" cy="2" r="2" fill="#fff"/><circle cx="2" cy="6" r="2" fill="#fff"/><circle cx="10" cy="10" r="2" fill="#fff"/><path d="M10 2L2 6l8 4" stroke="#fff" fill="none"/></svg>Online</div>
</div>
<div class="socials abs"><span></span><span></span><span></span></div>
<div class="map abs" role="img" aria-label="Street map marking the office location"></div>

<footer class="site-footer abs">
  <nav class="footer-nav">
    <a style="left:190px">Home</a>
    <a style="left:256px">Marketing Catalysts</a>
    <a style="left:382px">Our Formula</a>
    <a style="left:477px">Chemical Reactions</a>
    <a style="left:603px">Contact us</a>
  </nav>
  <span class="copyright abs">All Rights Reserved. Copyrights @ 2016 company name</span>
  <span class="page-mark abs">M1</span>
</footer>

</body>
</html>
```